Health and Fitness Club requires membership pack

We need a membership pack, like this style (http://www.sheetmakersvault.co.uk/images/A4_pocket_folder_round.jpg) a4 sized.

The front of it should contain our logo, the entire thing should be in the style of our brand/concept. On the inside left side there should be space for copy which we will provide once the design has been selected (approximately 500 words).

At the bottom of the left page inside, should be the following:
telephone icon | zqt icon
pixelbrook logo | chirpnet logo | vuo logo | email logo

with the relevant contact details for our company, underneath this should be our website written so that it occupies the entire width of the page.

our website is www. v o r t a g r i p . ae and our logo is attached

i have included a flyer we recently produced to give you an idea of the creative direction of the brand..

```html
<!DOCTYPE html>
<html lang="en">
<head>
<meta charset="utf-8">
<title>Vortagrip Membership Pack – Pocket Folder Layout</title>
<link rel="stylesheet" href="https://fonts.googleapis.com/css2?family=Montserrat:wght@300;600&display=swap">
<style>
  :root {
    --paper: #ffffff;
    --trim-line: #c8c8c8;
    --fold-line: #ec3d9c;
    --brand-red: #a3232f;
    --ink: #111111;
  }
  html, body {
    margin: 0;
    padding: 0;
    width: 1200px;
    height: 1081px;
    overflow: hidden;
    background: var(--paper);
  }
  .folder-dieline {
    display: block;
    width: 1200px;
    height: 1081px;
  }
  .panel-outline, .pocket-outline {
    fill: var(--paper);
    stroke: var(--trim-line);
    stroke-width: 1;
  }
  .fold-line {
    fill: none;
    stroke: var(--fold-line);
    stroke-width: 1.3;
    stroke-dasharray: 9 6;
  }
  .glue-flap {
    fill: url(#glue-hatch);
    stroke: var(--fold-line);
    stroke-width: 1.3;
  }
  .glue-hatch-line {
    stroke: var(--fold-line);
    stroke-width: 1;
  }
  .contact-band { fill: var(--brand-red); }
  .brand-text {
    font-family: "Montserrat", sans-serif;
    font-weight: 300;
    fill: var(--ink);
  }
  .logo-name { font-size: 15px; letter-spacing: 1px; }
  .logo-ring { fill: none; stroke: var(--ink); stroke-width: 2; }
  .channel-label {
    font-size: 11px;
    font-weight: 600;
  }
  .channel-marker { fill: var(--ink); }
  .channel-icon { fill: var(--ink); }
  .channel-icon-stroke { fill: none; stroke: var(--brand-red); stroke-width: 1.2; }
  .website-line { font-size: 22px; }
</style>
</head>
<body>
<svg class="folder-dieline" width="1200" height="1081" viewBox="0 0 1200 1081" xmlns="http://www.w3.org/2000/svg">
  <defs>
    <pattern id="glue-hatch" patternUnits="userSpaceOnUse" width="12" height="12" patternTransform="rotate(-45)">
      <line class="glue-hatch-line" x1="0" y1="0" x2="0" y2="12"/>
    </pattern>
  </defs>

  <!-- Front cover and inside spread -->
  <rect class="panel-outline" x="63.5" y="72.5" width="1045" height="725"/>

  <!-- Pocket -->
  <path class="pocket-outline" d="M648 797 C 660 960, 780 1050, 900 1050 L 1108 1050 L 1108 797 Z"/>

  <!-- Glue flap -->
  <path class="glue-flap" d="M1108 797 L 1145 815 L 1145 1035 L 1108 1050 Z"/>

  <!-- Fold lines -->
  <line class="fold-line" x1="587" y1="72" x2="587" y2="797"/>
  <line class="fold-line" x1="648" y1="797" x2="1108" y2="797"/>
  <line class="fold-line" x1="1108" y1="797" x2="1108" y2="1050"/>

  <!-- Brand mark -->
  <g class="brand-mark">
    <circle class="logo-ring" cx="325" cy="322" r="22"/>
    <text class="brand-text logo-name" x="325" y="375" text-anchor="middle">VORTAGRIP</text>
  </g>

  <!-- Contact band -->
  <rect class="contact-band" x="63" y="718" width="524" height="79"/>

  <g class="contact-channels">
    <!-- phone -->
    <path class="channel-icon" d="M191 734 l3 -1 l2.5 4 l-2 1.5 c1 2.5 2.5 4 5 5 l1.5 -2 l4 2.5 l-1 3 c-7.5 0 -13 -5.5 -13 -13 z"/>

    <rect class="channel-marker" x="214" y="735" width="8" height="8"/>
    <text class="brand-text channel-label" x="225" y="746">zqt</text>

    <rect class="channel-marker" x="254" y="735" width="8" height="8"/>
    <text class="brand-text channel-label" x="265" y="746">pixelbrook</text>

    <rect class="channel-marker" x="333" y="735" width="8" height="8"/>
    <text class="brand-text channel-label" x="344" y="746">chirpnet</text>

    <rect class="channel-marker" x="402" y="735" width="8" height="8"/>
    <text class="brand-text channel-label" x="413" y="746">vuo</text>

    <!-- email -->
    <rect class="channel-icon" x="444" y="735" width="15" height="11"/>
    <path class="channel-icon-stroke" d="M444 735.5 l7.5 6 l7.5 -6"/>
  </g>

  <text class="brand-text website-line" x="100" y="784" textLength="453" lengthAdjust="spacing">www. v o r t a g r i p . ae</text>
</svg>
</body>
</html>
```